Brookvale Estates LLC stationary for a real estate property management company.

Create stationary (letterhead, envelopes, business cards) using Brookvale Estates LLC logo as primary creative element. Stationary design needs to be horizontal, leaving as much space as possible for correspondence copy. See attached Creative Brief and past stationary files for details.

Target Market(s)

Prospective apartment residents and current residents, vendors, and government agencies.

Industry/Entity Type

Property Management

Contact Information for Business Card

Business card employee title: Property Manager. Should include address, phone, fax, email, website, slogan, and Brookvale Estates logo.

Font styles to use
Sans Serif

Colors
0592cd
000000

Requirements
Must have
• Tone should be conservative, institutional, business (i.e. banking, finance, real estate). Must include: address, phone, fax, website, and slogan (see attached Creative Brief). Should be a horizontal design, leaving as much room as possible for letter correspondence copy.
Nice to have
• Please use an Arial or Helvetica style font.
Should not have
• Letterhead layout should leave as much room as possible for copy.

```html
<!DOCTYPE html>
<html lang="en">
<head>
<meta charset="utf-8">
<title>Brookvale Estates LLC – Business Card</title>
<link href="https://fonts.googleapis.com/css2?family=Arimo:wght@400;700&display=swap" rel="stylesheet">
<style>
  :root {
    --backdrop: #e9e7e4;
    --card-blue: #0b69a6;
    --brand-blue: #1576ba;
    --panel-grey: #3f4044;
    --paper: #f6f6f6;
    --ink-white: #ffffff;
    --mark-grey: #5a5b5f;
  }
  * { margin: 0; padding: 0; box-sizing: border-box; }
  html, body { width: 1200px; height: 960px; overflow: hidden; }
  body {
    position: relative;
    background: var(--backdrop);
    font-family: "Arimo", Arial, Helvetica, sans-serif;
  }
  .card {
    position: absolute;
    width: 601px;
    height: 341px;
    overflow: hidden;
    box-shadow: 0 2px 6px rgba(0,0,0,0.35);
  }
  .card-front { left: 302px; top: 130px; background: var(--card-blue); color: var(--ink-white); }
  .card-back { left: 298px; top: 489px; width: 601px; background: var(--paper); }

  .front-panel { position: absolute; inset: 0; }

  .company-name {
    position: absolute; left: 36px; top: 38px;
    font-weight: 700; line-height: 1;
  }
  .company-name .line-main { display: block; font-size: 38px; letter-spacing: 0.5px; }
  .company-name .line-sub { display: block; font-size: 19px; letter-spacing: 3px; margin-top: 4px; }

  .person-name { position: absolute; left: 36px; top: 118px; font-size: 21px; font-weight: 700; }
  .person-title { position: absolute; left: 36px; top: 143px; font-size: 15px; }
  .address { position: absolute; left: 36px; top: 175px; font-size: 14px; line-height: 18px; }

  .contact-list { position: absolute; left: 38px; top: 210px; list-style: none; font-size: 14px; }
  .contact-list li { display: flex; align-items: center; height: 19px; }
  .contact-list svg { width: 12px; height: 12px; margin-right: 10px; fill: var(--ink-white); }

  .slogan { position: absolute; left: 36px; top: 293px; font-size: 14px; font-weight: 700; }

  .back-mark {
    position: absolute; left: 0; right: 0; top: 0; bottom: 0;
    display: flex; align-items: center; justify-content: center; gap: 16px;
  }
  .back-mark .mark-square { width: 58px; height: 58px; background: var(--mark-grey); }
  .back-mark .wordmark { color: var(--brand-blue); font-weight: 700; line-height: 1; }
  .back-mark .line-main { display: block; font-size: 42px; }
  .back-mark .line-sub { display: block; font-size: 19px; letter-spacing: 4px; margin-top: 6px; }
</style>
</head>
<body>

<section class="card card-front" aria-label="Business card, front">
  <svg class="front-panel" viewBox="0 0 601 341" aria-hidden="true">
    <circle cx="560" cy="200" r="262" fill="var(--panel-grey)"/>
  </svg>

  <div class="company-name">
    <span class="line-main">BROOKVALE</span>
    <span class="line-sub">ESTATES LLC</span>
  </div>

  <div class="person-name">DANIEL HARLOW</div>
  <div class="person-title">Property Manager</div>
  <div class="address">2750 Alder Creek Road #B210<br>Fresno, CA 93711</div>

  <ul class="contact-list">
    <li><svg viewBox="0 0 12 12"><path d="M2.5 0.5l2 2.2-1 1.3c.6 1.5 1.9 2.9 3.5 3.6l1.3-1 2.2 2-1.2 1.9C5 10.2 1.7 6.9 0.6 1.7z"/></svg>559-410-2738</li>
    <li><svg viewBox="0 0 12 12"><rect x="3" y="0.5" width="6" height="3"/><rect x="0.5" y="4" width="11" height="5" rx="1"/><rect x="3" y="8" width="6" height="3.5" fill="var(--card-blue)" stroke="#fff" stroke-width="1"/></svg>559-410-2739</li>
    <li><svg viewBox="0 0 12 12"><rect x="0.5" y="2" width="11" height="8"/><path d="M0.5 2l5.5 4.5L11.5 2" fill="none" stroke="var(--card-blue)" stroke-width="1.2"/></svg>daniel@brookvaleestates.us</li>
    <li><svg viewBox="0 0 12 12"><circle cx="6" cy="6" r="5.5"/><path d="M0.5 6h11M6 0.5c-2.5 3-2.5 8 0 11M6 0.5c2.5 3 2.5 8 0 11" fill="none" stroke="var(--card-blue)" stroke-width="0.9"/></svg>www.brookvaleestates.us</li>
  </ul>

  <div class="slogan">Multifamily Property Management</div>
</section>

<section class="card card-back" aria-label="Business card, back">
  <div class="back-mark">
    <span class="mark-square" aria-hidden="true"></span>
    <span class="wordmark">
      <span class="line-main">BROOKVALE</span>
      <span class="line-sub">ESTATES LLC</span>
    </span>
  </div>
</section>

</body>
</html>
```